Growing the Ironclad Young Contender:
A Family Playbook for Nurturing Bold, Grounded, and Resilient Daughters at Games and Beyond.
📘 Book Cover Design Brief – “Growing the Ironclad Young Contender”

Project Title:
Design a bold, inspiring book cover for a best-selling book titled:
Growing the Ironclad Young Contender
Subtitle: A Family Playbook for Nurturing Bold, Grounded, and Resilient Daughters at Games and Beyond

🎯 Audience:

Parents of female athletes ages 14–20 who want their daughters to build confidence, strength, resilience, and long-term success both in sports and in life.

This book should feel encouraging, empowering, and credible — NOT cheesy, childish, or overly academic.

📕 Design Tone & Style:

Powerful and professional — should feel like a best-selling book from a leading performance or parenting expert

Emotionally compelling — conveys hope, resilience, strength, and possibility

Visually modern and clean — avoid anything overly busy, cliché, or childish

Heroic/aspirational tone — think transformation, leadership, strong positioning

💡 Visual Direction / Ideas (Use as Inspiration, Not Limitation):

Strong, confident teenage female athlete imagery — adaptable beyond one specific sport

Symbolic visuals — e.g. athlete standing strong, on a starting line, looking bold into the future, silhouette, or power stance

Bold typography that feels clean and modern (e.g., Proxima Nova, Montserrat, Gotham, Bebas Neue, etc.)

A title that stands out clearly when viewed as a thumbnail on Brindlemart

Color tones: Empowering, modern, and strong: think deep blues, greens, purples, or golds — avoid playful pastels or overly girly themes

Potential imagery: textured backgrounds, motion, bravery, development, strength, growth, sport/action overlays

🔥 What the Cover MUST Communicate:

✅ This is for parents who want strong, confident female athletes
✅ It’s a guidebook for personal development AND sports performance
✅ It’s about creating “IRONCLAD” confidence — physically, mentally and emotionally
✅ The message is: You can help your daughter become her strongest, most confident self

📚 Back-of-Book Summary (for context):

"Growing the Ironclad Young Contender" is a parent's blueprint to building girls who are strong in body, confident in mind, and ready to lead on and off the field. Through simple strategies around strength training, mindset, nutrition, and character development, this book gives parents the tools to help their daughters stay injury-resistant, break through mental barriers, and unlock their full potential — in sports and in life.

✅ Deliverables:

Full cover design (front, back, spine) for paperback
High-resolution files (print-ready)
Source files (PSD, AI, etc.)
3D mockup versions of the book (standing, flat, stack)

Target Market(s)

Industry/Entity Type

Fitness

Font styles to use
Sans Serif

Colors
FFF300
FFF600
FEFA6F
FFFEC7
FFFEE8

Requirements
Must have
• Bold Font
Should not have
• I don't want an image of a female athlete. I want this to be font based.

```html
<!DOCTYPE html>
<html lang="en">
<head>
<meta charset="utf-8">
<title>Growing the Ironclad Young Contender – Full Cover</title>
<link href="https://fonts.googleapis.com/css2?family=Bebas+Neue&family=Oswald:wght@200;300&display=swap" rel="stylesheet">
<style>
  :root {
    --gold: #ffe27a;
    --white: #ffffff;
    --night: #0b1a30;
    --sky: #2b4a72;
    --dusk: #7b6a5a;
    --sun: #ffb347;
    --ground: #050607;
    --portrait: #1c1c1e;
  }
  * { margin: 0; padding: 0; box-sizing: border-box; }
  html, body { width: 1200px; height: 854px; overflow: hidden; background: var(--ground); }
  .cover {
    position: relative;
    width: 1200px;
    height: 854px;
    overflow: hidden;
    font-family: "Bebas Neue", "Oswald", sans-serif;
    color: var(--gold);
  }
  .scenery {
    position: absolute; inset: 0;
    background:
      radial-gradient(ellipse 220px 120px at 925px 458px, rgba(255,214,120,0.95), rgba(255,170,70,0.55) 40%, rgba(255,150,60,0) 100%),
      radial-gradient(ellipse 700px 220px at 820px 450px, rgba(240,160,90,0.45), rgba(240,160,90,0) 100%),
      linear-gradient(180deg, var(--night) 0%, #16315a 22%, var(--sky) 40%, var(--dusk) 52%, #2a2520 60%, #0f0f10 75%, var(--ground) 100%);
  }
  /* Back cover */
  .back {
    position: absolute; left: 101px; top: 156px; width: 371px;
    display: flex; flex-direction: column; align-items: center;
  }
  .blurb {
    width: 100%;
    font-size: 18px; line-height: 23.1px;
    text-align: justify; text-align-last: left;
    text-transform: uppercase; letter-spacing: 0;
  }
  .author-photo {
    width: 133px; height: 166px; margin-top: 8px;
    border: 2px solid var(--gold);
    background: radial-gradient(ellipse at 50% 40%, #3a3a3d, var(--portrait) 70%);
  }
  .bio {
    width: 100%; margin-top: 12px;
    font-size: 14.6px; line-height: 18.4px;
    text-align: justify; text-align-last: left;
    text-transform: uppercase;
  }
  .barcode-area {
    position: absolute; left: 315px; top: 685px; width: 195px; height: 105px;
    background: var(--white);
  }
  /* Spine */
  .spine {
    position: absolute; left: 588px; top: 152px; height: 545px;
    writing-mode: vertical-rl;
    display: flex; justify-content: space-between;
    font-size: 23px; line-height: 23px;
    text-transform: uppercase; white-space: nowrap;
  }
  .spine-author { font-size: 27px; }
  /* Front cover */
  .front {
    position: absolute; left: 700px; top: 96px; width: 420px;
    text-align: center; text-transform: uppercase;
  }
  .front h1 { font-weight: 400; }
  .title-lead, .title-key, .title-tail { display: block; }
  .title-lead {
    font-family: "Oswald", sans-serif; font-weight: 200;
    font-size: 58px; line-height: 62px;
  }
  .title-key {
    font-size: 90px; line-height: 78px; margin-top: 4px;
    text-shadow: 0 2px 6px rgba(0,0,0,0.35);
  }
  .title-tail {
    font-size: 70px; line-height: 66px;
    text-shadow: 0 2px 6px rgba(0,0,0,0.35);
  }
  .subtitle {
    position: absolute; left: 700px; top: 590px; width: 420px;
    text-align: center; color: var(--white);
    text-transform: uppercase; white-space: nowrap;
  }
  .subtitle span { display: block; }
  .sub-1 { font-size: 33px; line-height: 36px; }
  .sub-2 { font-size: 31px; line-height: 36px; }
  .sub-3 { font-size: 26px; line-height: 32px; }
  .sub-4 { font-size: 21px; line-height: 28px; }
  .front-author {
    position: absolute; left: 700px; top: 746px; width: 420px;
    text-align: center; font-size: 48px; line-height: 48px;
  }
</style>
</head>
<body>
<main class="cover">
  <div class="scenery" role="img" aria-label="Sunset sky over a valley with a winding river, an athlete in a power stance silhouetted on a rocky ridge"></div>

  <section class="back">
    <p class="blurb">"Growing the Ironclad Young Contender" is a parent's blueprint to building girls who are strong in body, confident in mind, and ready to lead on and off the field. Through simple strategies around strength training, mindset, nutrition, and character development, this book gives parents the tools to help their daughters stay injury-resistant, break through mental barriers, and unlock their full potential — in sports and in life.</p>
    <div class="author-photo" role="img" aria-label="Author portrait of Dalton Brewer against a dark backdrop"></div>
    <p class="bio">Dalton has 15 years experience, specializing in personal training and sport performance. He focuses his training on creating programs that improve performance and reduce the risk of injury. Dalton has worked with clients from 8 – 73. He is a 2 time Brindlemart best-selling author with Rise Strong Now and Peak Fuel for Varsity Competitors. Dalton commits his life to coaching each client to be great. Stride Works was born out of his passion to make each person who walks in the door the very best version of themselves.</p>
  </section>
  <div class="barcode-area"></div>

  <section class="spine">
    <span class="spine-title">Growing the Ironclad Young Contender</span>
    <span class="spine-author">Dalton Brewer</span>
  </section>

  <section class="front">
    <h1>
      <span class="title-lead">Growing the</span>
      <span class="title-key">Ironclad</span>
      <span class="title-tail">Young Contender</span>
    </h1>
  </section>
  <p class="subtitle">
    <span class="sub-1">A Family Playbook</span>
    <span class="sub-2">for Nurturing Bold,</span>
    <span class="sub-3">Grounded, and Resilient</span>
    <span class="sub-4">Daughters at Games and Beyond</span>
  </p>
  <p class="front-author">Dalton Brewer</p>
</main>
</body>
</html>
```